I need a business card for my original fine art pieces

I would like a business card design including a logo design for a new business in the art world. I am based in the Hunter Valley NSW Australia. I am a contemporary figurative, encaustic and wildlife artist. I would like to be able to upload my email and mobile number to this as well. This design should be one that I can incorporate into banners and flyers etc. Id like to incorporate one of my own images or partial image into the background or somewhere below. My initials are RJ and I would like these used as a logo type. I would like the use of some colour and it to be bright and catchy. The final design should communicate artwork custom made and commissions available.

Overview: Original Fine Artworks for sale, online, art galleries etc, Custom made to order and by commission.

Target market is world wide audience and corporate world

My figurative work is painted using acrylics in a lot of natural ochre colours that reflect the Australian Outback, on canvas, linen, paper or board: My encaustic work is created in a contemporary abstract style using a blow torch and a made with a medium of 100% pure bees wax, Damar resin, mixed media and coloured pigments, applied to Birch board. My wildlife are created using coloured pencil and mixed media on a variety of paper types or board.

```html
<!DOCTYPE html>
<html lang="en">
<head>
<meta charset="utf-8">
<title>Rhea Jarvis – Business Card</title>
<link rel="stylesheet" href="https://fonts.googleapis.com/css2?family=Montserrat:wght@500&family=Open+Sans:wght@400;600&display=swap">
<style>
  :root {
    --page: #ece8e2;
    --charcoal: #333333;
    --orange: #ff4800;
    --black: #060606;
    --white: #ffffff;
  }
  * { box-sizing: border-box; margin: 0; padding: 0; }
  html, body { width: 1200px; height: 900px; overflow: hidden; }
  body {
    background: var(--page);
    position: relative;
    font-family: "Open Sans", Arial, sans-serif;
  }
  .card {
    position: absolute;
    width: 560px;
    height: 320px;
    overflow: hidden;
    box-shadow: 0 6px 18px rgba(0,0,0,.18);
  }

  /* Front */
  .card-front {
    left: 70px; top: 110px;
    background: var(--charcoal);
    display: flex; flex-direction: column; align-items: center;
    padding-top: 48px;
  }
  .brand-dot {
    width: 96px; height: 96px;
    border-radius: 50%;
    background: var(--orange);
  }
  .brand-name {
    margin-top: 22px;
    font-family: "Montserrat", Arial, sans-serif;
    font-weight: 500;
    font-size: 36px;
    line-height: 1;
    color: var(--orange);
    letter-spacing: 2px;
  }
  .brand-tagline {
    margin-top: 8px;
    font-family: "Montserrat", Arial, sans-serif;
    font-weight: 500;
    font-size: 17px;
    letter-spacing: 4px;
    color: var(--white);
  }
  .brand-web {
    margin-top: 14px;
    font-size: 13px;
    color: var(--white);
  }

  /* Back */
  .card-back { left: 570px; top: 470px; background: var(--charcoal); }
  .band-orange {
    position: absolute; left: 0; top: 92px; width: 100%; height: 160px;
    background: var(--orange);
  }
  .band-black {
    position: absolute; left: 0; top: 252px; width: 100%; height: 68px;
    background: var(--black);
  }
  .logo-disc {
    position: absolute; left: 202px; top: 14px;
    width: 156px; height: 156px; border-radius: 50%;
    background: var(--charcoal);
    display: flex; align-items: center; justify-content: center;
  }
  .logo-name {
    font-family: "Open Sans", Arial, sans-serif;
    font-weight: 600;
    font-size: 20px;
    color: var(--orange);
  }
  .contact-row {
    position: absolute; left: 0; top: 174px; width: 100%;
    display: flex; justify-content: center; align-items: center;
    color: var(--white);
  }
  .person { text-align: right; padding-right: 14px; border-right: 1px solid rgba(255,255,255,.55); }
  .person-name { font-weight: 600; font-size: 17px; line-height: 1.2; }
  .person-role { font-size: 14px; line-height: 1.2; }
  .details { padding-left: 12px; font-size: 13px; line-height: 1.55; }
  .details li { list-style: none; display: flex; align-items: center; gap: 6px; }
  .details svg { width: 11px; height: 11px; fill: var(--white); }
  .back-web {
    position: absolute; left: 0; top: 222px; width: 100%;
    text-align: center; font-size: 14px; color: var(--white);
  }
</style>
</head>
<body>

<section class="card card-front">
  <div class="brand-dot"></div>
  <h1 class="brand-name">RHEA JARVIS</h1>
  <p class="brand-tagline">ORIGINAL FINE ARTWORKS</p>
  <p class="brand-web">www.rheajarvis.art</p>
</section>

<section class="card card-back">
  <div class="band-orange"></div>
  <div class="band-black"></div>
  <div class="logo-disc"><span class="logo-name">Rhea Jarvis</span></div>
  <div class="contact-row">
    <div class="person">
      <p class="person-name">Daniel Hart</p>
      <p class="person-role">Managing Director</p>
    </div>
    <ul class="details">
      <li><svg viewBox="0 0 16 16" aria-hidden="true"><path d="M3 1l3 3-2 2c1 2 4 5 6 6l2-2 3 3-2 2C7 15 1 9 1 3z"/></svg>(044)987650321</li>
      <li><svg viewBox="0 0 16 16" aria-hidden="true"><path d="M1 3h14v10H1zM2 4l6 5 6-5v-.5H2z" fill-rule="evenodd"/></svg>hello@rheajarvis.art</li>
    </ul>
  </div>
  <p class="back-web">www.rheajarvis.art</p>
</section>

</body>
</html>
```